Business Card Design

New business card design

Target Market(s)

Residential & Commercial Property Managers

Industry/Entity Type

Plumbing Services

Contact Information for Business Card

Name - Rowan Keddle, title - Director, Phone Number - 0431 286 517, email - rowan@tbk-plumbing.com.au, Company ABN - 73 215 904 386,

Font styles to use
Sans Serif

Colors
0054AA
0677BA
7BADD7
CADEEF
E8F1F8

```html
<!DOCTYPE html>
<html lang="en">
<head>
<meta charset="utf-8">
<title>TBK Plumbing Services – Business Card</title>
<link rel="stylesheet" href="https://fonts.googleapis.com/css2?family=Krona+One&family=Poppins:wght@400;500;600&display=swap">
<style>
  :root {
    --page-bg: #b3b3b3;
    --card-bg: #ffffff;
    --ink: #111111;
    --logo-ink: #1c2530;
    --tagline-ink: #6b5a52;
    --accent: #0aa6e8;
    --navy-deep: #00183d;
    --navy: #0054aa;
    --blue-mid: #0677ba;
    --pipe-light: #cadeef;
  }
  * { box-sizing: border-box; margin: 0; padding: 0; }
  html, body {
    width: 1200px; height: 1200px; overflow: hidden;
    background: var(--page-bg);
    font-family: "Poppins", Arial, sans-serif;
  }
  .card {
    position: absolute;
    left: 174px;
    width: 865px;
    height: 494px;
    background: var(--card-bg);
    overflow: hidden;
  }
  .card--front { top: 92px; }
  .card--back { top: 627px; }

  .pipe-artwork {
    position: absolute;
    top: 0; right: 0;
    width: 255px; height: 100%;
    background:
      linear-gradient(90deg, rgba(255,255,255,0) 0, rgba(255,255,255,0) 100%),
      linear-gradient(160deg, var(--navy-deep) 0%, #022a63 40%, var(--navy) 75%, var(--blue-mid) 100%);
  }

  .brand {
    position: absolute;
    color: var(--logo-ink);
    font-family: "Poppins", Arial, sans-serif;
    font-weight: 500;
    line-height: 1;
    text-align: center;
  }
  .brand__name { display: block; letter-spacing: 0.04em; }
  .brand__tagline { display: block; color: var(--tagline-ink); font-weight: 400; }

  .card--front .brand { left: 88px; top: 150px; width: 440px; }
  .card--front .brand__name { font-size: 118px; }
  .card--front .brand__tagline { font-size: 17px; letter-spacing: 0.95em; margin-top: 22px; padding-left: 0.95em; }

  .card--back .brand { left: 52px; top: 80px; width: 196px; }
  .card--back .brand__name { font-size: 52px; }
  .card--back .brand__tagline { font-size: 8px; letter-spacing: 0.95em; margin-top: 8px; padding-left: 0.95em; }

  .person { position: absolute; left: 56px; top: 203px; }
  .person__name {
    font-family: "Krona One", Arial, sans-serif;
    font-size: 33px;
    line-height: 1;
    color: var(--ink);
    letter-spacing: -0.01em;
    white-space: nowrap;
  }
  .person__surname { color: var(--accent); }
  .person__role {
    font-size: 19px;
    font-weight: 500;
    letter-spacing: 0.12em;
    color: var(--ink);
    margin-top: 2px;
  }

  .contacts { position: absolute; left: 54px; top: 285px; list-style: none; }
  .contacts__item {
    display: flex; align-items: center; gap: 6px;
    font-size: 20px; font-weight: 600; color: var(--ink);
    height: 36px; margin-bottom: 9px;
  }
  .contacts__icon { width: 28px; height: 36px; flex: none; }

  .abn { position: absolute; left: 57px; top: 380px; font-size: 17px; font-weight: 600; color: var(--ink); }
  .abn__label { color: var(--accent); }
</style>
</head>
<body>

<section class="card card--front">
  <div class="brand">
    <span class="brand__name">tbk</span>
    <span class="brand__tagline">plumbing services</span>
  </div>
  <div class="pipe-artwork" role="img" aria-label="Illustration of light blue water pipes with a leaking joint, a valve and water droplets on a deep navy background"></div>
</section>

<section class="card card--back">
  <div class="brand">
    <span class="brand__name">tbk</span>
    <span class="brand__tagline">plumbing services</span>
  </div>

  <div class="person">
    <h1 class="person__name">ROWAN <span class="person__surname">KEDDLE</span></h1>
    <p class="person__role">Director</p>
  </div>

  <ul class="contacts">
    <li class="contacts__item">
      <svg class="contacts__icon" viewBox="0 0 28 36" aria-hidden="true">
        <path d="M14 1 C18 8 26 14 26 22 A12 12 0 0 1 2 22 C2 14 10 8 14 1 Z" fill="#fff" stroke="#0aa6e8" stroke-width="2"/>
        <path d="M10 18 l2.5 -1 1.5 3 -1.5 1 q1 2.5 3.5 3.5 l1 -1.5 3 1.5 -1 2.5 q-5 0 -9 -9 z" fill="#111"/>
      </svg>
      <span>0431 286 517</span>
    </li>
    <li class="contacts__item">
      <svg class="contacts__icon" viewBox="0 0 28 36" aria-hidden="true">
        <path d="M14 1 C18 8 26 14 26 22 A12 12 0 0 1 2 22 C2 14 10 8 14 1 Z" fill="#fff" stroke="#0aa6e8" stroke-width="2"/>
        <rect x="8" y="19" width="12" height="8" fill="#111"/>
        <path d="M8 19 l6 5 6 -5" fill="none" stroke="#fff" stroke-width="1.2"/>
      </svg>
      <span>rowan@tbk-plumbing.com.au</span>
    </li>
  </ul>

  <p class="abn"><span class="abn__label">Company ABN</span> - 73 215 904 386</p>

  <div class="pipe-artwork" role="img" aria-label="Illustration of light blue water pipes with a leaking joint, a valve and water droplets on a deep navy background"></div>
</section>

</body>
</html>
```